Business Card for Industrial Distributor

We need a business card design for an industrial distributor. We sell machine parts for the manufacturing and oil industry. We would like the cards to look clean and modern but with a touch of industry.

Our colors are blue/white.

Please feel free to visit our website www.korvelpartsco.com

Target Market(s)

mexican manufacturers in the automobile/aerospace industry

Industry/Entity Type

Industrial

Colors
ffffff
0555a3

```html
<!DOCTYPE html>
<html lang="en">
<head>
<meta charset="utf-8">
<title>Korvel Business Card</title>
<link href="https://fonts.googleapis.com/css2?family=Lato:wght@400;900&family=Exo+2:wght@500&display=swap" rel="stylesheet">
<style>
  :root {
    --brand-blue: #0555a3;
    --brand-navy: #2b3990;
    --paper: #ffffff;
    --text-grey: #8a8a8a;
    --stage: #3b3b3b;
  }
  html, body {
    margin: 0;
    padding: 0;
    width: 1200px;
    height: 810px;
    overflow: hidden;
    background: var(--stage);
  }
  .canvas {
    position: relative;
    width: 1200px;
    height: 810px;
  }
  .card {
    position: absolute;
    width: 560px;
    height: 320px;
    overflow: hidden;
    box-shadow: 0 6px 18px rgba(0,0,0,0.35);
  }
  /* Back of card */
  .card-back {
    left: 60px;
    top: 60px;
    background: var(--brand-blue);
  }
  .card-back .brand {
    position: absolute;
    left: 0;
    right: 0;
    top: 112px;
    display: flex;
    align-items: center;
    justify-content: center;
    gap: 16px;
  }
  .brand-dot {
    width: 52px;
    height: 52px;
    border-radius: 50%;
  }
  .card-back .brand-dot { background: var(--paper); }
  .brand-name {
    font-family: 'Lato', sans-serif;
    font-weight: 900;
    font-size: 66px;
    letter-spacing: -1px;
    line-height: 1;
  }
  .card-back .brand-name { color: var(--paper); }
  .card-back .site {
    position: absolute;
    left: 0;
    right: 0;
    top: 218px;
    text-align: center;
    font-family: 'Lato', sans-serif;
    font-size: 13px;
    color: var(--paper);
    letter-spacing: 0.3px;
  }
  /* Front of card */
  .card-front {
    left: 580px;
    top: 430px;
    background: var(--paper);
  }
  .card-front .brand {
    position: absolute;
    left: 34px;
    top: 36px;
    display: flex;
    align-items: center;
    gap: 12px;
  }
  .card-front .brand-dot {
    width: 44px;
    height: 44px;
    background: var(--brand-blue);
  }
  .card-front .brand-name {
    color: var(--brand-navy);
    font-size: 54px;
  }
  .holder {
    position: absolute;
    right: 40px;
    top: 70px;
    text-align: right;
  }
  .holder-name {
    font-family: 'Exo 2', sans-serif;
    font-weight: 500;
    font-size: 24px;
    color: var(--brand-blue);
    line-height: 1.1;
  }
  .holder-title {
    font-family: 'Lato', sans-serif;
    font-size: 12px;
    color: var(--text-grey);
    margin-top: 2px;
  }
  .contact {
    position: absolute;
    left: 36px;
    top: 180px;
    font-family: 'Lato', sans-serif;
    font-size: 13px;
    color: var(--text-grey);
    line-height: 1.35;
  }
  .address { margin-bottom: 10px; }
  .contact-line {
    display: flex;
    align-items: center;
    gap: 7px;
  }
  .contact-line svg {
    width: 13px;
    height: 13px;
    fill: var(--brand-blue);
    flex: none;
  }
  .wave {
    position: absolute;
    left: 0;
    bottom: 0;
    width: 560px;
    height: 150px;
  }
  .card-front .site {
    position: absolute;
    right: 28px;
    bottom: 92px;
    font-family: 'Lato', sans-serif;
    font-size: 12px;
    color: var(--paper);
    transform: rotate(-14deg);
    transform-origin: right bottom;
  }
</style>
</head>
<body>
<main class="canvas">

  <section class="card card-back" aria-label="Card back">
    <div class="brand">
      <span class="brand-dot"></span>
      <span class="brand-name">Korvel</span>
    </div>
    <div class="site">www.korvelpartsco.com</div>
  </section>

  <section class="card card-front" aria-label="Card front">
    <div class="brand">
      <span class="brand-dot"></span>
      <span class="brand-name">Korvel</span>
    </div>

    <div class="holder">
      <div class="holder-name">Daniel Reyes</div>
      <div class="holder-title">Presedent &amp; CEO</div>
    </div>

    <div class="contact">
      <div class="address">4120 Harbor Mill Rd,<br>Laredo, TX 78041</div>
      <div class="contact-line">
        <svg viewBox="0 0 24 24" aria-hidden="true"><path d="M6.6 10.8a15 15 0 0 0 6.6 6.6l2.2-2.2a1 1 0 0 1 1-.25 11.4 11.4 0 0 0 3.6.57 1 1 0 0 1 1 1V20a1 1 0 0 1-1 1A17 17 0 0 1 3 4a1 1 0 0 1 1-1h3.5a1 1 0 0 1 1 1c0 1.25.2 2.45.57 3.6a1 1 0 0 1-.25 1z"/></svg>
        <span>(555) 318 - 4720</span>
      </div>
      <div class="contact-line">
        <svg viewBox="0 0 24 24" aria-hidden="true"><path d="M6 2h10v5H6zM3 8h18a1 1 0 0 1 1 1v8h-4v5H6v-5H2V9a1 1 0 0 1 1-1zm5 9v3h8v-3z"/></svg>
        <span>(555) 318 - 4726</span>
      </div>
      <div class="contact-line">
        <svg viewBox="0 0 24 24" aria-hidden="true"><path d="M2 5h20v14H2zm2 2v.5l8 5 8-5V7l-8 5z"/></svg>
        <span>sales@korvelpartsco.com</span>
      </div>
    </div>

    <svg class="wave" viewBox="0 0 560 150" preserveAspectRatio="none" aria-hidden="true">
      <path d="M0 150 L0 140 C120 150 200 130 300 80 C390 35 470 18 560 12 L560 150 Z" fill="var(--brand-blue)"/>
      <path d="M0 136 C120 146 200 124 300 74 C390 30 470 12 560 6" fill="none" stroke="var(--brand-blue)" stroke-width="1.5" opacity="0.6"/>
    </svg>
    <div class="site">www.korvelpartsco.com</div>
  </section>

</main>
</body>
</html>
```